Figure for presentation on a hybrid research project

We need a figure that shows a series of 6 technical projects feeding into 3 multidisciplinary hybrid projects.
The concept is a ring of 6 technical projects, which could look like a 6 colour swirl (see
https://en.plorvanex.org/wiki/Vector_graphics for an example of a 4 colour swirl.)
The 3 hybrid projects sit in the centre because they rely on input from many of the surrounding technical projects.
I've drawn a rough version in Powerpoint - see attached file uploaded. Note, in my example I couldn't draw the swirling outer ring and the colour selection is poor. The acronym for the overall Centre using the figure is VexORDA, so we will have a mint leaf and turquoise green in the logo, plus also nerves, since we will be researching neural interconnections.
We ABSOLUTELY NEED the final form of the figure to include vector graphics formats (including a form that can be edited in Photoshop) because we may need to change the title of the technical projects or of the hybrid projects at short notice ourselves.

Target Market(s)

Academic: eminent scientists and engineers

Industry/Entity Type

Technical

Font styles to use
Sans Serif

Colors
04a990

Requirements
Must have
• The projects around the ring with all project titles legible; the final figure will be reduced to no more than 8cm x 8cm in the proposal (probably less).
• Only one colour selected, because we have included that colour in the logo that we are having designed. Otherwise, a colour series around the ring that is pleasant, and another compatible colour series for the inter 3 projects.
• We ABSOLUTELY NEED the final form of the figure to include vector graphics formats (including a form that can be edited in Photoshop) because we may need to change the title of the technical projects or of the hybrid projects at short notice ourselves.
Nice to have
• See the figure we uploaded; that's the essence
• HOWEVER VIP: two of the titles around the outer ring have changed slightly.
• Computational Modelling is now Neuronal Modelling and
• Signal Processing is now Non-Invasive Interfaces (note that I've now changed the titles on the uploaded figure)

```html
<!DOCTYPE html>
<html lang="en">
<head>
<meta charset="utf-8">
<title>VexORDA – Technical and Hybrid Projects</title>
<link rel="stylesheet" href="https://fonts.googleapis.com/css2?family=Lexend:wght@600;700&display=swap">
<style>
  :root {
    --page-bg: #ffffff;
    --divider: #ffffff;
    --teal-deep: #086b55;
    --teal-brand: #05a088;
    --teal-mid: #0a7d65;
    --teal-bright: #06977f;
    --teal-dark: #07684f;
    --teal-soft: #069c84;
    --hub-wiring: #6cc600;
    --hub-action: #8800d8;
    --hub-perception: #a6a300;
    --label: #ffffff;
  }
  html, body {
    margin: 0;
    padding: 0;
    width: 1200px;
    height: 999px;
    overflow: hidden;
    background: var(--page-bg);
  }
  .figure {
    display: block;
    width: 1200px;
    height: 999px;
  }
  .petal {
    stroke: var(--divider);
    stroke-width: 4;
    stroke-linejoin: round;
  }
  .petal--living { fill: var(--teal-deep); }
  .petal--gene { fill: var(--teal-brand); }
  .petal--electro { fill: var(--teal-mid); }
  .petal--optrode { fill: var(--teal-bright); }
  .petal--neuronal { fill: var(--teal-dark); }
  .petal--noninvasive { fill: var(--teal-soft); }
  .project-title {
    font-family: "Lexend", sans-serif;
    font-weight: 600;
    font-size: 23px;
    fill: var(--label);
  }
  .hub-ring {
    fill: none;
    stroke: var(--divider);
    stroke-width: 5;
  }
  .hub-sector { stroke: var(--divider); stroke-width: 3; }
  .hub-sector--wiring { fill: var(--hub-wiring); }
  .hub-sector--action { fill: var(--hub-action); }
  .hub-sector--perception { fill: var(--hub-perception); }
  .hybrid-title {
    font-family: "Lexend", sans-serif;
    font-weight: 700;
    font-size: 20px;
    fill: var(--label);
    text-anchor: middle;
  }
</style>
</head>
<body>
<svg class="figure" viewBox="0 0 1130 941" xmlns="http://www.w3.org/2000/svg" role="img" aria-label="Six technical projects in a swirling ring around three hybrid projects">
  <defs>
    <filter id="hub-shadow" x="-20%" y="-20%" width="140%" height="140%">
      <feDropShadow dx="0" dy="0" stdDeviation="10" flood-color="#003a2e" flood-opacity="0.45"/>
    </filter>
    <path id="arc-living" d="M296.2,318.4 A195,195 0 0,1 633.4,300.7"/>
    <path id="arc-gene" d="M559.4,165.7 A195,195 0 0,1 743.3,448.9"/>
    <path id="arc-noninvasive" d="M296.8,622.7 A195,195 0 0,1 450.1,321.8"/>
    <path id="arc-electro" d="M670.8,635.2 A212,212 0 0,0 837.5,308.0"/>
    <path id="arc-optrode" d="M472.3,648.6 A212,212 0 0,0 839.0,629.3"/>
    <path id="arc-neuronal" d="M361.5,483.4 A212,212 0 0,0 561.5,791.3"/>
  </defs>

  <g class="technical-ring">
    <path class="petal petal--living" d="M214.0,439.7 A258,258 0 1,1 716.2,483.7 A258,258 0 0,0 214.0,439.7 Z"/>
    <path class="petal petal--gene" d="M413.2,155.2 A258,258 0 1,1 626.3,612.1 A258,258 0 0,0 413.2,155.2 Z"/>
    <path class="petal petal--electro" d="M759.2,185.5 A258,258 0 1,1 470.1,598.5 A258,258 0 0,0 759.2,185.5 Z"/>
    <path class="petal petal--optrode" d="M906.0,500.3 A258,258 0 1,1 403.8,456.3 A258,258 0 0,0 906.0,500.3 Z"/>
    <path class="petal petal--neuronal" d="M706.8,784.8 A258,258 0 1,1 493.7,327.9 A258,258 0 0,0 706.8,784.8 Z"/>
    <path class="petal petal--noninvasive" d="M360.8,754.5 A258,258 0 1,1 649.9,341.5 A258,258 0 0,0 360.8,754.5 Z"/>
  </g>

  <g class="technical-titles">
    <text class="project-title"><textPath href="#arc-living" startOffset="50%" text-anchor="middle">Living Electrodes</textPath></text>
    <text class="project-title"><textPath href="#arc-gene" startOffset="50%" text-anchor="middle">Gene Regulated Interfaces</textPath></text>
    <text class="project-title"><textPath href="#arc-electro" startOffset="50%" text-anchor="middle">Electro-modulated Interfaces</textPath></text>
    <text class="project-title"><textPath href="#arc-optrode" startOffset="50%" text-anchor="middle">Optrode Interfaces</textPath></text>
    <text class="project-title"><textPath href="#arc-neuronal" startOffset="50%" text-anchor="middle">Neuronal Modeling</textPath></text>
    <text class="project-title"><textPath href="#arc-noninvasive" startOffset="50%" text-anchor="middle">Non-invasive Interfaces</textPath></text>
  </g>

  <g class="hybrid-hub" filter="url(#hub-shadow)">
    <path class="hub-sector hub-sector--wiring" d="M560,470 L404.1,380 A180,180 0 0,1 715.9,380 Z"/>
    <path class="hub-sector hub-sector--perception" d="M560,470 L715.9,380 A180,180 0 0,1 560,650 Z"/>
    <path class="hub-sector hub-sector--action" d="M560,470 L560,650 A180,180 0 0,1 404.1,380 Z"/>
    <circle class="hub-ring" cx="560" cy="470" r="182"/>
  </g>

  <g class="hybrid-titles">
    <text class="hybrid-title" x="559" y="380">BRAIN WIRING</text>
    <text class="hybrid-title" x="472" y="518">ACTION</text>
    <text class="hybrid-title" x="646" y="518">PERCEPTION</text>
  </g>
</svg>
</body>
</html>
```